We need a web page design for a new company called "Brambel". We provide an innovative music sharing mobile application that allows music listeners to share their music without paying for a monthly subscription. We would like to incorporate the attached logo and color scheme. The final design should communicate music gifting and sharing.

Industry/Entity Type

It Company

```html
<!DOCTYPE html>
<html lang="en">
<head>
<meta charset="utf-8">
<title>Brambel — Music Sharing</title>
<link href="https://fonts.googleapis.com/css2?family=Roboto:ital,wght@0,400;0,500;0,700;1,400;1,700&display=swap" rel="stylesheet">
<style>
:root{
  --green:#5ea40e;
  --green-dark:#4f8f0a;
  --green-mid:#6aad1e;
  --green-light:#8cc04b;
  --orange:#f7941d;
  --grey:#8f8f8f;
  --text:#333;
  --cream:#ece7d8;
  --footer:#333333;
  --footer-deep:#262626;
  --white:#fff;
}
*{box-sizing:border-box;margin:0;padding:0}
html,body{width:821px;height:1200px;overflow:hidden;background:var(--white)}
body{font-family:"Roboto",Arial,sans-serif;color:var(--text);position:relative}
.abs{position:absolute}

/* header */
.site-header{position:absolute;left:0;top:0;width:821px;height:60px;background:var(--green)}
.brand{position:absolute;left:122px;top:10px;display:flex;align-items:center;gap:8px;color:var(--white);font-size:30px;font-weight:500}
.brand-dot{width:28px;height:28px;border-radius:50%;background:var(--white)}
.main-nav{position:absolute;left:379px;top:0;display:flex;height:60px}
.main-nav a{display:block;padding:0 14px;line-height:78px;height:60px;font-size:10px;font-weight:700;color:var(--white);text-decoration:none}
.main-nav a.active{background:var(--white);color:var(--text);padding:0 11px}
.account-links{position:absolute;left:680px;top:13px;font-size:8px;color:var(--white);letter-spacing:.3px}

/* hero */
.hero{position:absolute;left:0;top:60px;width:821px;height:263px;background:linear-gradient(180deg,#8b5a2e 0%,#7a4a22 55%,#5d3518 100%)}
.hero-slide{position:absolute;left:566px;top:125px;width:172px;height:97px;background:rgba(240,240,240,.55);text-align:center}
.hero-slide .badge{position:absolute;left:62px;top:-20px;width:48px;height:42px;background:var(--green);border-radius:50%}
.hero-slide .title{position:absolute;left:0;right:0;top:28px;font-size:20px;font-weight:700;color:#333}
.hero-controls{position:absolute;left:41px;top:66px;display:flex;height:18px}
.hero-controls span{background:var(--green);color:var(--white);font-size:8px;line-height:18px;padding:0 6px}
.hero-controls .more{background:#4b4b4b;padding:0 5px}

/* features */
.features{position:absolute;left:113px;top:323px;width:640px;height:130px;display:flex}
.feature{position:relative;width:160px;height:130px;color:var(--white);text-align:center}
.feature:nth-child(odd){background:var(--green-mid)}
.feature:nth-child(even){background:var(--green-light)}
.feature .ring{position:absolute;left:38px;top:-41px;width:84px;height:84px;border-radius:50%;background:var(--white);border:3px solid var(--green-mid);display:flex;align-items:center;justify-content:center}
.feature h3{position:absolute;left:0;right:0;top:52px;font-size:12px;font-weight:700}
.feature p{position:absolute;left:14px;right:14px;top:70px;font-size:9px;line-height:11px}
.feature .plus{position:absolute;left:70px;top:112px;width:20px;height:18px;background:var(--orange);border:2px solid var(--white);border-bottom:0;color:var(--white);font-size:15px;line-height:15px;font-weight:700}

/* section headings */
.section-title{position:absolute;left:113px;font-size:14px;border-left:2px solid var(--green);padding-left:4px;line-height:16px;color:#333}
.pager{position:absolute;display:flex;gap:1px}
.pager span{width:15px;height:15px;font-size:10px;line-height:15px;text-align:center;color:var(--white)}

/* trending */
.track{position:absolute;top:510px;width:148px}
.cover{width:148px;height:148px;padding:5px}
.cover div{width:100%;height:100%}
.track .caption{font-size:8.5px;font-style:italic;font-weight:700;margin-top:4px;white-space:nowrap}
.track .actions{display:flex;justify-content:space-between;margin-top:5px;padding-bottom:7px;border-bottom:2px solid var(--green)}
.btn{font-size:8px;font-weight:500;color:var(--white);height:14px;line-height:14px;padding:0 6px}
.btn-share{background:var(--green-mid)}
.btn-gift{background:var(--grey);width:40px;text-align:center}

/* call to action */
.cta{position:absolute;left:113px;top:726px;width:640px;height:60px;background:var(--cream);border:1px solid #d8d2c0}
.cta p{position:absolute;left:6px;top:20px;font-size:14px;color:#444}
.cta .btn-signup{position:absolute;left:543px;top:16px;width:86px;height:25px;background:var(--green-mid);color:var(--white);font-size:10px;font-weight:700;text-align:center;line-height:25px}

/* categories */
.read-more{position:absolute;left:684px;top:815px;width:67px;height:19px;background:var(--orange);color:#333;font-size:8px;font-weight:700;text-align:center;line-height:19px}
.cat-rule{position:absolute;left:113px;top:844px;width:640px;height:1px;background:#e8e8e8}
.category-col{position:absolute;top:857px;width:82px}
.category-col li{list-style:none;height:26.7px;font-size:9px;color:#444;display:flex;align-items:center;gap:5px;border-bottom:1px solid #eee;position:relative}
.category-col li::before{content:"";width:9px;height:9px;border-radius:50%;background:#cfcfcf;flex:none}
.category-col li::after{content:"›";position:absolute;right:-2px;top:5px;color:var(--green);font-size:14px;font-weight:700}
.category-col li.current{color:var(--green-mid)}

/* footer */
.site-footer{position:absolute;left:0;top:1038px;width:821px;height:134px;background:var(--footer);border-top:2px solid var(--green);color:var(--white)}
.footer-col h4{position:absolute;font-size:12.5px;font-weight:400}
.quick-links{position:absolute;left:113px;top:37px;list-style:none;font-size:8.5px;line-height:14.4px}
.quick-links li::before{content:"›  "}
.news-item{position:absolute;left:229px;display:flex;gap:6px}
.date{width:24px;text-align:center;font-size:9px;font-weight:700}
.date .d{background:var(--green-mid);height:14px;line-height:14px}
.date .m{background:#eee;color:#333;font-size:6px;height:9px;line-height:9px}
.news-item p{font-size:8px;line-height:10px}
.news-item b{font-size:8.5px}
.email{position:absolute;left:430px;top:68px;width:142px;height:18px;background:var(--white);color:#888;font-size:7px;font-style:italic;padding:5px 4px}
.btn-subscribe{position:absolute;left:430px;top:94px;width:72px;height:19px;background:var(--green-mid);font-size:10px;font-weight:700;text-align:center;line-height:19px}
.footer-brand{position:absolute;left:621px;top:38px;display:flex;align-items:center;gap:6px;font-size:26px;font-weight:500}
.footer-brand .brand-dot{width:24px;height:24px}
.social{position:absolute;left:642px;top:95px;display:flex;gap:8px}
.social span{width:15px;height:15px;border-radius:50%;background:#555}
.social span.on{background:var(--green-mid)}
.copyright{position:absolute;left:0;top:1172px;width:821px;height:28px;background:var(--footer-deep);color:#ddd;font-size:8px;text-align:center;line-height:30px}
</style>
</head>
<body>

<header class="site-header">
  <div class="brand"><span class="brand-dot"></span>Brambel</div>
  <nav class="main-nav">
    <a class="active" href="#">HOME</a><a href="#">SERVICES</a><a href="#">TIMETABLE</a><a href="#">NEWS</a><a href="#">FEATURES</a><a href="#">CONTACTS</a>
  </nav>
  <div class="account-links">LOGIN &nbsp;|&nbsp; SIGNUP</div>
</header>

<section class="hero" role="img" aria-label="Photo of a wooden desk with sheet music, two speakers showing sharing and headphone icons, a guitar pedal and an amplifier">
  <div class="hero-slide">
    <div class="badge"></div>
    <div class="title">Brambel</div>
    <div class="hero-controls"><span>&lt;</span><span class="more">READ MORE</span><span>&gt;</span></div>
  </div>
</section>

<section class="features">
  <div class="feature">
    <div class="ring"><svg width="34" height="34" viewBox="0 0 34 34"><path d="M11 6 L29 2 V24" stroke="#f7941d" stroke-width="4" fill="none"/><path d="M11 6 V28" stroke="#f7941d" stroke-width="4"/><circle cx="7" cy="28" r="5" fill="#f7941d"/><circle cx="25" cy="24" r="5" fill="#f7941d"/></svg></div>
    <h3>UPLOAD MUSIC &amp; AUDIO</h3><p>Lorem Ipsum is simply dummy text of the printing.</p><div class="plus">+</div>
  </div>
  <div class="feature">
    <div class="ring"><svg width="40" height="36" viewBox="0 0 40 36"><path d="M5 22 V18 A15 15 0 0 1 35 18 V22" stroke="#f7941d" stroke-width="4" fill="none"/><rect x="3" y="19" width="9" height="15" rx="3" fill="#f7941d"/><rect x="28" y="19" width="9" height="15" rx="3" fill="#f7941d"/></svg></div>
    <h3>LISTEN &amp; DISCOVER</h3><p>Lorem Ipsum is simply dummy text of the printing fdsjoid.</p><div class="plus">+</div>
  </div>
  <div class="feature">
    <div class="ring"><svg width="40" height="36" viewBox="0 0 40 36"><circle cx="15" cy="9" r="7" fill="#f7941d"/><path d="M2 34 A13 13 0 0 1 28 34Z" fill="#f7941d"/><circle cx="29" cy="18" r="5" fill="#f7941d"/><path d="M20 34 A9 9 0 0 1 38 34Z" fill="#f7941d"/></svg></div>
    <h3>CONNECT</h3><p>Lorem Ipsum is simply dummy text of the printing.</p><div class="plus">+</div>
  </div>
  <div class="feature">
    <div class="ring"><svg width="40" height="36" viewBox="0 0 40 36"><path d="M8 8 L20 18 L33 8 M20 18 L10 30 M20 18 L32 28" stroke="#f7941d" stroke-width="3"/><circle cx="20" cy="18" r="6" fill="#f7941d"/><circle cx="8" cy="8" r="5" fill="#f7941d"/><circle cx="33" cy="8" r="4" fill="#f7941d"/><circle cx="10" cy="30" r="4" fill="#f7941d"/><circle cx="32" cy="28" r="5" fill="#f7941d"/></svg></div>
    <h3>SHARE</h3><p>Lorem Ipsum is simply dummy text of the printing fdsjoid.</p><div class="plus">+</div>
  </div>
</section>

<h2 class="section-title" style="top:483px">TRENDING MUSIC &amp; AUDIO</h2>
<div class="pager" style="left:719px;top:483px"><span style="background:#ccc">‹</span><span style="background:var(--green-mid)">›</span></div>

<article class="track" style="left:113px">
  <div class="cover" style="background:var(--green-mid)"><div role="img" aria-label="Black and white album cover art" style="background:linear-gradient(160deg,#9a9a9a,#3c3c3c)"></div></div>
  <p class="caption">Lorem ipsum dolor sfgjit rem Ipsumis</p>
  <div class="actions"><span class="btn btn-share">SHARE</span><span class="btn btn-gift">GIFT</span></div>
</article>
<article class="track" style="left:277px">
  <div class="cover" style="background:var(--orange)"><div role="img" aria-label="Dark album cover art with copper lettering and a play button" style="background:radial-gradient(circle,#6e3a22,#111 70%)"></div></div>
  <p class="caption">Lorem ipsum dolor sfgjit rem Ipsumis</p>
  <div class="actions" style="border-color:#aaa"><span class="btn btn-share">SHARE</span><span class="btn btn-gift">GIFT</span></div>
</article>
<article class="track" style="left:440px">
  <div class="cover" style="background:var(--green-mid)"><div role="img" aria-label="Pink and white album cover art" style="background:linear-gradient(135deg,#e8288f,#f7d3e6 60%,#e8288f)"></div></div>
  <p class="caption">Lorem ipsum dolor sfgjit rem Ipsumis</p>
  <div class="actions"><span class="btn btn-share">SHARE</span><span class="btn btn-gift">GIFT</span></div>
</article>
<article class="track" style="left:604px">
  <div class="cover" style="background:var(--green-mid)"><div role="img" aria-label="Dark gold fantasy album cover art" style="background:radial-gradient(circle,#b08a3a,#3a2a12 75%)"></div></div>
  <p class="caption">Lorem ipsum dolor sfgjit rem Ipsumis</p>
  <div class="actions"><span class="btn btn-share">SHARE</span><span class="btn btn-gift">GIFT</span></div>
</article>

<aside class="cta">
  <p>So are you ready to discover new music and sounds and share them with the world?</p>
  <div class="btn-signup">SIGN UP NOW</div>
</aside>

<h2 class="section-title" style="top:817px">MUSIC CATEGORIES</h2>
<div class="read-more">READ MORE</div>
<div class="cat-rule"></div>

<ul class="category-col" style="left:113px"><li class="current">Acoustic</li><li>Music-Pack</li><li>Drum'n' Bass</li><li>Alternative</li><li>Eurodance</li><li>Ambient</li></ul>
<ul class="category-col" style="left:220px"><li>Acoustic</li><li>Music-Pack</li><li>Drum'n' Bass</li><li>Alternative</li><li>Eurodance</li><li>Ambient</li></ul>
<ul class="category-col" style="left:329px"><li>Acoustic</li><li>Music-Pack</li><li>Drum'n' Bass</li><li>Alternative</li><li>Eurodance</li><li>Ambient</li></ul>
<ul class="category-col" style="left:439px"><li>Acoustic</li><li>Music-Pack</li><li>Drum'n' Bass</li><li>Alternative</li><li>Eurodance</li><li>Ambient</li></ul>
<ul class="category-col" style="left:552px"><li>Acoustic</li><li>Music-Pack</li><li>Drum'n' Bass</li><li>Alternative</li><li>Eurodance</li><li>Ambient</li></ul>
<ul class="category-col" style="left:667px"><li>Acoustic</li><li>Music-Pack</li><li>Drum'n' Bass</li><li>Alternative</li><li>Eurodance</li><li>Ambient</li></ul>

<footer class="site-footer">
  <div class="footer-col"><h4 style="left:113px;top:12px">Quick Links</h4>
    <ul class="quick-links"><li>Home</li><li>Services</li><li>Timetable</li><li>News</li><li>Features</li><li>Contact Us</li></ul>
  </div>
  <div class="footer-col"><h4 style="left:229px;top:12px">News Updates</h4>
    <div class="pager" style="left:362px;top:15px"><span style="background:var(--green-mid);width:11px;height:11px;line-height:11px">‹</span><span style="background:var(--green-mid);width:11px;height:11px;line-height:11px">›</span></div>
    <div class="news-item" style="top:42px"><div class="date"><div class="d">12</div><div class="m">NOV</div></div><p><b>Vero eros accumsaet odio</b><br>quis nostrud exetiperj suscipit<br>nisl ut aliquip ex ea commod</p></div>
    <div class="news-item" style="top:90px"><div class="date"><div class="d">20</div><div class="m">NOV</div></div><p><b>Vero eros accumsaet odio</b><br>quis nostrud exetiperj suscipit<br>nisl ut aliquip ex ea commod</p></div>
  </div>
  <div class="footer-col"><h4 style="left:430px;top:12px">Newsletter Sign Up</h4>
    <p class="abs" style="left:430px;top:37px;font-size:8px;line-height:13px">Lorem ipsudolor sit coec adipiscing<br>elitsite amet</p>
    <div class="email">Email Address</div>
    <div class="btn-subscribe">SUBSCRIBE</div>
  </div>
  <div class="footer-brand"><span class="brand-dot"></span>Brambel</div>
  <div class="social" aria-label="Social links"><span></span><span class="on"></span><span></span><span></span></div>
</footer>
<div class="copyright">© 2014 <b>BrambelMusic</b>. All Rights Reserved.</div>

</body>
</html>
```